KBT Business Cards

We require business cards for our business. We would like a matte black back to the card, with our logo centred in the middle. The front side of the card is open to design.

Target Market(s)

Clients looking for legal services (professional)

Industry/Entity Type

Legal

Contact Information for Business Card

Doran Kelbrath
Partner
Mobile: 0461 738 524
Email: doran@kbtlaw.co
Website: www.kbtlaw.co
Level 3, 118 Wendmore Street
Sydney NSW 2000

Font styles to use
Other font styles liked:
• Avenir

Colors
f04a50
ffffff
1b1b1b

Requirements
Must have
• Black back with logo included in the centre of the card.
• Our font is Avenir.

```html
<!DOCTYPE html>
<html lang="en">
<head>
<meta charset="utf-8">
<title>KBT Business Cards</title>
<link rel="stylesheet" href="https://fonts.googleapis.com/css2?family=Nunito+Sans:wght@400;600;800&display=swap">
<style>
  :root {
    --red: #f04a50;
    --red-deep: #c8214a;
    --white: #ffffff;
    --black: #1b1b1b;
    --stage: #2b2b2b;
    --ink: #111111;
  }
  * { box-sizing: border-box; margin: 0; padding: 0; }
  html, body { width: 1200px; height: 960px; overflow: hidden; }
  body {
    background: var(--stage);
    font-family: "Nunito Sans", "Avenir", sans-serif;
    display: flex;
    flex-direction: column;
    align-items: center;
    justify-content: center;
    gap: 40px;
  }
  .card {
    width: 700px;
    height: 428px;
    position: relative;
    overflow: hidden;
    border-radius: 4px;
  }

  /* Back side */
  .card-back { background: var(--black); }
  .card-back .surface { position: absolute; inset: 0; background: radial-gradient(circle at 50% 45%, #262626, var(--black) 70%); }
  .back-brand {
    position: absolute; left: 0; right: 0; top: 140px;
    display: flex; align-items: center; justify-content: center; gap: 22px;
  }
  .brand-square { width: 64px; height: 64px; background: var(--red-deep); flex: none; }
  .brand-name {
    font-weight: 800; text-transform: uppercase;
    font-size: 30px; line-height: 1.02; letter-spacing: 0.5px;
  }
  .card-back .brand-name { color: var(--white); }
  .back-url {
    position: absolute; left: 0; right: 0; bottom: 70px;
    text-align: center; color: var(--white);
    font-size: 17px; letter-spacing: 6px;
  }
  .back-url .accent { color: var(--red-deep); font-weight: 800; }

  /* Front side */
  .card-front { background: var(--black); }
  .front-panel {
    position: absolute; left: 0; top: 0; bottom: 0; width: 318px;
    background: var(--white);
  }
  .front-divider { position: absolute; left: 300px; top: 0; width: 30px; height: 428px; }
  .front-brand {
    position: absolute; left: 34px; top: 130px;
    display: flex; align-items: center; gap: 16px;
  }
  .front-brand .brand-square { width: 52px; height: 52px; }
  .front-brand .brand-name { color: var(--ink); font-size: 25px; }
  .contact { position: absolute; left: 350px; top: 118px; color: var(--white); }
  .contact-name {
    color: var(--red-deep); font-weight: 800; font-size: 22px;
    text-transform: uppercase; letter-spacing: 0.8px; line-height: 1;
  }
  .contact-role { font-size: 14px; text-transform: uppercase; letter-spacing: 0.5px; margin-top: 4px; }
  .contact-list { list-style: none; margin-top: 24px; }
  .contact-list li {
    display: flex; align-items: center; gap: 12px;
    font-size: 17px; line-height: 1; margin-bottom: 13px;
  }
  .contact-list svg { width: 18px; height: 18px; flex: none; }
  .contact-address { font-size: 17px; line-height: 1.3; margin-top: 14px; }
</style>
</head>
<body>

  <section class="card card-back" aria-label="Card back">
    <div class="surface" role="img" aria-label="Matte black card surface"></div>
    <div class="back-brand">
      <span class="brand-square"></span>
      <span class="brand-name">Kelbrath<br>Bryce Tolan<br>Legal</span>
    </div>
    <p class="back-url">www.<span class="accent">kbtlaw</span>.co</p>
  </section>

  <section class="card card-front" aria-label="Card front">
    <div class="front-panel"></div>
    <svg class="front-divider" viewBox="0 0 30 428" aria-hidden="true">
      <path d="M18 0 V160 L8 170 L18 180 V428" fill="none" stroke="var(--red-deep)" stroke-width="3"/>
    </svg>
    <div class="front-brand">
      <span class="brand-square"></span>
      <span class="brand-name">Kelbrath<br>Bryce Tolan<br>Legal</span>
    </div>

    <div class="contact">
      <h1 class="contact-name">Doran Kelbrath</h1>
      <p class="contact-role">Partner</p>
      <ul class="contact-list">
        <li>
          <svg viewBox="0 0 18 18" aria-hidden="true"><circle cx="9" cy="9" r="8" fill="none" stroke="#fff" stroke-width="1.3"/><rect x="6.5" y="4.5" width="5" height="9" rx="1" fill="none" stroke="#fff" stroke-width="1.2"/></svg>
          0461 738 524
        </li>
        <li>
          <svg viewBox="0 0 18 18" aria-hidden="true"><rect x="1.5" y="4" width="15" height="10" fill="none" stroke="#fff" stroke-width="1.3"/><path d="M1.5 4 L9 10 L16.5 4" fill="none" stroke="#fff" stroke-width="1.3"/></svg>
          doran@kbtlaw.co
        </li>
        <li>
          <svg viewBox="0 0 18 18" aria-hidden="true"><circle cx="9" cy="9" r="7.5" fill="none" stroke="#fff" stroke-width="1.3"/><ellipse cx="9" cy="9" rx="3.3" ry="7.5" fill="none" stroke="#fff" stroke-width="1.1"/><path d="M1.5 9 H16.5 M3 5 H15 M3 13 H15" stroke="#fff" stroke-width="1"/></svg>
          www.kbtlaw.co
        </li>
      </ul>
      <p class="contact-address">Level 3, 118 Wendmore Street<br>Sydney NSW 2000</p>
    </div>
  </section>

</body>
</html>
```